Unique Business Card Design

Unique Business Card design for our orthotic and prosthetic company. Our logo is on our website, color is light blue. Unique shape (artificial leg shaped, vertical, etc..) preferred. Logo, business name, individual name and basic demographics needed.

Industry/Entity Type

Business

Contact Information for Business Card

Logo, Industry, Phone # Logo, "Prosthetic & Orthotic Services" Place to add individual name and contact info

Colors
cee9f5

Requirements
Must have
• The icon must be there, placement of "Prosthetic & Orthotic Services" can be moved
Nice to have
• Like the mix of light blue, and a little darker blue. One design included the icons from my website which was a nice touch

```html
<!DOCTYPE html>
<html lang="en">
<head>
<meta charset="utf-8">
<title>Limbwell Co – Business Card</title>
<link rel="stylesheet" href="https://fonts.googleapis.com/css2?family=Open+Sans:wght@400;600;700&family=Crimson+Text:ital@1&display=swap">
<style>
  :root {
    --page-bg: #cbcbcb;
    --card-light: #cee9f5;
    --brand-blue: #0a6fcf;
    --brand-blue-deep: #0867c2;
    --ink: #2e2e2e;
    --white: #ffffff;
  }
  * { margin: 0; padding: 0; box-sizing: border-box; }
  html, body { width: 1200px; height: 900px; overflow: hidden; }
  body {
    background: var(--page-bg);
    font-family: "Open Sans", Arial, sans-serif;
    position: relative;
  }
  .card {
    position: absolute;
    top: 170px;
    width: 347px;
    height: 561px;
    overflow: hidden;
  }
  .card--front { left: 259px; background: var(--card-light); }
  .card--back { left: 631px; background: var(--brand-blue); }

  .card__bands { position: absolute; inset: 0; }

  .brand-badge {
    position: absolute;
    left: 87px; top: 77px;
    width: 174px; height: 174px;
    border-radius: 50%;
    background: var(--brand-blue);
    display: flex; align-items: center; justify-content: center;
    color: var(--white);
    font-weight: 700;
    font-size: 19px;
    letter-spacing: 0.5px;
  }

  .contact {
    position: absolute;
    left: 0; right: 0; top: 326px;
    text-align: center;
    color: var(--ink);
  }
  .contact__name {
    color: var(--brand-blue);
    font-weight: 700;
    font-size: 20px;
    line-height: 28px;
  }
  .contact__title { font-size: 14.5px; line-height: 20px; }
  .contact__phone {
    margin-top: 12px;
    font-size: 16px; font-weight: 600; line-height: 22px;
    display: flex; justify-content: center; align-items: center; gap: 5px;
  }
  .contact__phone svg { width: 13px; height: 13px; fill: var(--brand-blue); }
  .contact__line { font-size: 15px; line-height: 21px; }
  .contact__line--first { margin-top: 5px; }
  .contact__address { margin-top: 6px; font-size: 14px; line-height: 17px; }

  .back-glow {
    position: absolute;
    left: -45px; top: 4px;
    width: 437px; height: 556px;
    border-radius: 50%;
    background: var(--brand-blue-deep);
  }
  .lockup {
    position: absolute;
    left: 28px; top: 242px;
    display: flex; align-items: center; gap: 20px;
  }
  .lockup__dot {
    width: 76px; height: 76px;
    border-radius: 50%;
    background: var(--white);
    flex: none;
  }
  .lockup__name {
    color: var(--white);
    font-size: 23px; font-weight: 600;
    line-height: 28px;
    padding-bottom: 4px;
    border-bottom: 1.5px solid var(--white);
    letter-spacing: 0.3px;
  }
  .lockup__tagline {
    color: var(--white);
    font-family: "Crimson Text", Georgia, serif;
    font-style: italic;
    font-size: 13.5px;
    margin-top: 4px;
    padding-left: 14px;
  }
</style>
</head>
<body>
  <section class="card card--front">
    <svg class="card__bands" viewBox="0 0 347 561" aria-hidden="true">
      <path d="M94 0 H253 V38 Q173.5 2 94 38 Z" fill="var(--brand-blue)"/>
      <path d="M94 561 H253 V523 Q173.5 559 94 523 Z" fill="var(--brand-blue)"/>
    </svg>
    <div class="brand-badge">LIMBWELL CO</div>
    <div class="contact">
      <p class="contact__name">ALEX MORGAN</p>
      <p class="contact__title">Managing Director</p>
      <p class="contact__phone">
        <svg viewBox="0 0 24 24" aria-hidden="true"><path d="M6.6 10.8a15.1 15.1 0 0 0 6.6 6.6l2.2-2.2a1 1 0 0 1 1-.25 11.4 11.4 0 0 0 3.6.57 1 1 0 0 1 1 1V20a1 1 0 0 1-1 1A17 17 0 0 1 3 4a1 1 0 0 1 1-1h3.5a1 1 0 0 1 1 1c0 1.25.2 2.45.57 3.6a1 1 0 0 1-.25 1z"/></svg>
        (555) 014-2290
      </p>
      <p class="contact__line contact__line--first">hello@limbwellco.com</p>
      <p class="contact__line">www.limbwellco.com</p>
      <p class="contact__address">1234, Address Goes Here Country<br>Name, 123456</p>
    </div>
  </section>

  <section class="card card--back">
    <div class="back-glow" aria-hidden="true"></div>
    <div class="lockup">
      <div class="lockup__dot" aria-hidden="true"></div>
      <div>
        <p class="lockup__name">LIMBWELL CO</p>
        <p class="lockup__tagline">Prosthetic &amp; Orthotic Services</p>
      </div>
    </div>
  </section>
</body>
</html>
```